IT Company needs full suite of stationery

Our company 4627 Vantor Holdings Inc. is an IT company based in Toronto, Canada. Based on our logo we would like to see business cards(front and back), letterhead, envelope, brochure template. Design would be simple, not too bright, modern but can be used for many years, good theme throughout. Our official logo is the the fullcolor_a, full company name is 4627 Vantor Holdings Inc., Please include full company name on all pieces. Logo can be modified to be the graphic only with the "4627 Holdings", I have cropped it myself for a couple files but I am no designer. We will provide lots of feedback so post early and often.

Project Deadline Extended
Reason: Very busy around the holidays, like a lot of the designs currently submitted, will definitely be picking one. Thanks for your submissions and merry Christmas and Happy New Year to everyone.

Industry/Entity Type

Business

```html
<!DOCTYPE html>
<html lang="en">
<head>
<meta charset="utf-8">
<title>4627 Holdings – Business Cards</title>
<link rel="stylesheet" href="https://fonts.googleapis.com/css2?family=Mulish:wght@400;700;800&display=swap">
<style>
  :root {
    --bg: #e9eaea;
    --card: #f7f7f7;
    --green: #4a9b2f;
    --green-dark: #1f6b2a;
    --green-light: #6cbf3a;
    --ink: #3a3a3a;
    --ink-soft: #5a5a5a;
    --shadow: rgba(0,0,0,0.16);
  }
  * { box-sizing: border-box; margin: 0; padding: 0; }
  html, body { width: 1200px; height: 900px; overflow: hidden; }
  body {
    background: var(--bg);
    font-family: "Mulish", sans-serif;
    color: var(--ink);
    position: relative;
  }
  .card {
    position: absolute;
    left: 320px;
    width: 560px;
    height: 320px;
    background: var(--card);
    box-shadow: 0 6px 18px var(--shadow);
    overflow: hidden;
  }
  .card--back { top: 100px; }
  .card--front { top: 480px; }

  .brand {
    display: flex;
    align-items: center;
    gap: 14px;
    white-space: nowrap;
  }
  .brand__dot {
    width: 58px; height: 58px;
    border-radius: 50%;
    background: var(--green);
    flex: none;
  }
  .brand__name {
    font-weight: 800;
    font-size: 30px;
    color: var(--ink);
    letter-spacing: 0.5px;
  }
  .card--back .brand {
    position: absolute;
    left: 50%; top: 50%;
    transform: translate(-50%, -50%);
  }

  .card--front .brand {
    position: absolute;
    left: 34px; top: 28px;
  }
  .brand--small .brand__dot { width: 48px; height: 48px; }
  .brand--small .brand__name { font-size: 25px; }

  .contact {
    position: absolute;
    left: 34px; top: 108px;
    list-style: none;
    font-size: 12.5px;
    color: var(--ink-soft);
    line-height: 20px;
  }
  .contact li { display: flex; align-items: center; gap: 9px; white-space: nowrap; }
  .contact svg { width: 12px; height: 12px; flex: none; }

  .rule {
    position: absolute;
    left: 34px; right: 34px; top: 186px;
    height: 1px;
    background: var(--green);
  }

  .person {
    position: absolute;
    right: 34px; top: 144px;
    text-align: right;
    white-space: nowrap;
  }
  .person__name { font-weight: 800; font-size: 18px; line-height: 22px; color: var(--ink); }
  .person__title { font-size: 13px; line-height: 18px; color: var(--green); }

  .address {
    position: absolute;
    right: 34px; top: 198px;
    text-align: right;
    font-size: 13px;
    font-style: normal;
    line-height: 19px;
    color: var(--ink-soft);
    white-space: nowrap;
  }

  .band {
    position: absolute;
    left: 0; right: 0; bottom: 0;
    height: 26px;
    background: linear-gradient(90deg, var(--green-dark), var(--green-light));
  }
</style>
</head>
<body>

  <section class="card card--back" aria-label="Business card back">
    <div class="brand">
      <span class="brand__dot"></span>
      <span class="brand__name">4627 Holdings</span>
    </div>
  </section>

  <section class="card card--front" aria-label="Business card front">
    <div class="brand brand--small">
      <span class="brand__dot"></span>
      <span class="brand__name">4627 Holdings</span>
    </div>

    <ul class="contact">
      <li>
        <svg viewBox="0 0 12 12" aria-hidden="true"><path d="M2.2 1 4 1 5 3.6 3.9 4.6C4.5 6 5.9 7.5 7.4 8.1L8.4 7 11 8v1.8C11 10.5 10.5 11 9.8 11 5 10.7 1.3 7 1 2.2 1 1.5 1.5 1 2.2 1Z" fill="var(--green)"/></svg>
        +1 416 555 0142
      </li>
      <li>
        <svg viewBox="0 0 12 12" aria-hidden="true"><path d="M2.2 1 4 1 5 3.6 3.9 4.6C4.5 6 5.9 7.5 7.4 8.1L8.4 7 11 8v1.8C11 10.5 10.5 11 9.8 11 5 10.7 1.3 7 1 2.2 1 1.5 1.5 1 2.2 1Z" fill="var(--green)"/></svg>
        +1 416 555 0187
      </li>
      <li>
        <svg viewBox="0 0 12 12" aria-hidden="true"><rect x="0.8" y="2.3" width="10.4" height="7.4" fill="none" stroke="var(--green)" stroke-width="1.2"/><path d="M0.8 2.6 6 6.6 11.2 2.6" fill="none" stroke="var(--green)" stroke-width="1.2"/></svg>
        ceo@vantorholdings.example
      </li>
    </ul>

    <div class="person">
      <p class="person__name">Daniel Okafor</p>
      <p class="person__title">CEO</p>
    </div>

    <div class="rule"></div>

    <address class="address">
      4627 Vantor Holdings Inc.<br>
      210 Harlow Street M5V 2T6<br>
      Toronto, Canada
    </address>

    <div class="band"></div>
  </section>

</body>
</html>
```